A clean crisp business card for a Landscape Construction company. Designed to be easy to read contact/ info and also be appealing/interesting, unlike a traditional business card.

Industry/Entity Type

Landscape Construction

Contact Information for Business Card

Company name : Brambleford Landscape Construction, phone number: (877) 62Vista, website:Bramblefordyards.example, Email, sales@bramblefordyards.example

Requirements
Nice to have
• Luxurious finishes/ details…. Icons or emblems next to contact info
Should not have
• Clipart or general pictures

```html
<!DOCTYPE html>
<html lang="en">
<head>
<meta charset="utf-8">
<title>Brambleford Landscape Construction – Business Card</title>
<link href="https://fonts.googleapis.com/css2?family=Cinzel:wght@400;600&family=Arimo:wght@400&display=swap" rel="stylesheet">
<style>
  :root {
    --stage: #e9eaec;
    --card-dark: #1b1b1b;
    --brand-blue: #1a6fc9;
    --brand-green: #9dcc3b;
    --back-blue: #166cc1;
    --back-ink: #0e559f;
    --text-light: #f2f2f2;
    --text-soft: #d8d8d8;
    --rule: #4a4a4a;
  }
  * { box-sizing: border-box; margin: 0; padding: 0; }
  html, body { width: 1093px; height: 1200px; overflow: hidden; }
  body { background: var(--stage); position: relative; font-family: "Arimo", Arial, sans-serif; }

  .card {
    position: absolute; left: 257px; width: 579px; height: 357px; overflow: hidden;
    box-shadow: 0 2px 6px rgba(0,0,0,.25);
  }
  .card--front { top: 226px; background: var(--card-dark); }
  .card--back { top: 620px; background: var(--back-blue); }

  .brand { position: absolute; right: 26px; top: 122px; text-align: right; }
  .brand__name {
    display: flex; align-items: center; justify-content: flex-end; gap: 10px;
    font-family: "Cinzel", serif; font-weight: 600; font-size: 34px; letter-spacing: .5px;
    color: var(--brand-blue); line-height: 1;
  }
  .brand__dot { width: 16px; height: 16px; border-radius: 50%; background: var(--brand-green); }
  .brand__tagline {
    margin-top: 8px; font-family: "Cinzel", serif; font-weight: 600; font-size: 13px;
    letter-spacing: 3.9px; color: var(--brand-green);
  }

  .person { position: absolute; left: 28px; top: 192px; right: 29px; }
  .person__name { font-family: "Cinzel", serif; font-weight: 600; font-size: 25px; color: var(--brand-blue); line-height: 1; }
  .person__name span { color: var(--brand-green); }
  .person__role { display: flex; align-items: center; gap: 6px; margin-top: 5px; font-size: 15px; color: var(--brand-green); }
  .person__role::after { content: ""; flex: 1; height: 1px; background: var(--rule); }

  .contacts { position: absolute; left: 28px; top: 258px; list-style: none; }
  .contacts li { display: flex; align-items: center; gap: 5px; height: 21px; font-size: 16px; color: var(--text-light); }
  .contacts svg { width: 15px; height: 15px; flex: none; }
  .contacts .accent { color: var(--brand-blue); }

  .address { position: absolute; right: 29px; top: 279px; text-align: right; font-size: 16px; line-height: 21px; color: var(--text-soft); font-style: normal; }

  .bands { position: absolute; left: 0; bottom: 0; width: 579px; height: 32px; }

  .back-brand { position: absolute; left: 0; right: 0; top: 208px; text-align: center; }
  .back-brand__name { font-family: "Cinzel", serif; font-weight: 600; font-size: 40px; letter-spacing: .5px; color: var(--back-ink); line-height: 1; }
  .back-brand__tagline { margin-top: 10px; font-family: "Cinzel", serif; font-weight: 600; font-size: 15px; letter-spacing: 4.6px; color: var(--back-ink); }
</style>
</head>
<body>

<section class="card card--front">
  <div class="brand">
    <div class="brand__name"><span class="brand__dot"></span>Brambleford</div>
    <div class="brand__tagline">LANDSCAPE CONSTRUCTION</div>
  </div>

  <div class="person">
    <div class="person__name">Owen <span>Hartley</span></div>
    <div class="person__role">MANAGING DIRECTOR</div>
  </div>

  <ul class="contacts">
    <li>
      <svg viewBox="0 0 16 16" aria-hidden="true"><path fill="var(--brand-blue)" d="M3.6 1.5l2.3 2.7-1.3 1.7c.9 2 2.4 3.5 4.4 4.4l1.7-1.3 2.7 2.3-1.2 2.3C7.2 13.6 2.4 8.8 1.4 3.8z"/><path d="M9.5 2.5a4 4 0 0 1 4 4M9.5 0.5a6 6 0 0 1 6 6" stroke="var(--brand-blue)" stroke-width="1.2" fill="none"/></svg>
      (877) 62Vista
    </li>
    <li>
      <svg viewBox="0 0 16 16" aria-hidden="true"><rect x="1" y="3.5" width="14" height="9" fill="var(--brand-blue)"/><path d="M1 3.5l7 5 7-5" stroke="var(--card-dark)" stroke-width="1.2" fill="none"/></svg>
      sales@bramblefordyards.example
    </li>
    <li>
      <svg viewBox="0 0 16 16" aria-hidden="true"><g fill="none" stroke="var(--brand-blue)" stroke-width="1.2"><circle cx="8" cy="8" r="6.5"/><ellipse cx="8" cy="8" rx="3" ry="6.5"/><path d="M1.5 8h13M2.5 4.8h11M2.5 11.2h11"/></g></svg>
      <span><span class="accent">Bramblefordyards</span>.example</span>
    </li>
  </ul>

  <address class="address">
    86 Fernhollow Road<br>30917, Ashgrove Vale
  </address>

  <svg class="bands" viewBox="0 0 579 32" aria-hidden="true">
    <polygon points="0,18 286,18 282,32 0,32" fill="var(--brand-blue)"/>
    <polygon points="300,0 579,0 579,30 289,30" fill="var(--brand-green)"/>
  </svg>
</section>

<section class="card card--back">
  <div class="back-brand">
    <div class="back-brand__name">Brambleford</div>
    <div class="back-brand__tagline">LANDSCAPE CONSTRUCTION</div>
  </div>
</section>

</body>
</html>
```